BRISKEL Need a luxury modern business card designed.

Need a luxury modern business card designed. refer to the uploaded files for the company name and logo in the zip file under source files. i will making my descion on monday. so please send in before then so if we need to edit we will have the time. we have a trade show coming up and im on a deadline for printer.

Target Market(s)

high end clients

Contact Information for Business Card

Company nAme and logo. Tobias Fennick Co-Founder / Project Manager Office # 555-318-7094 Cell # 555-642-1586 BRISKEL.CA Tobias@briskel-example.ca

Font styles to use
Other font styles liked:
• Modern

Requirements
Must have
• Company name and logo, contact info, using the black, gold and white color scheme.

```html
<!DOCTYPE html>
<html lang="en">
<head>
<meta charset="utf-8">
<title>BRISKEL Business Card</title>
<link href="https://fonts.googleapis.com/css2?family=Josefin+Sans:wght@300;400&family=Raleway:wght@600&family=Arimo:wght@400&display=swap" rel="stylesheet">
<style>
  :root {
    --bg: #2a2a2b;
    --card: #1e1f21;
    --gold: #a8986a;
    --white: #f2f2f2;
    --rule: #6a6a6a;
  }
  * { box-sizing: border-box; margin: 0; padding: 0; }
  html, body { width: 1200px; height: 1108px; overflow: hidden; }
  body {
    background: var(--bg);
    display: flex;
    align-items: center;
    justify-content: center;
    gap: 60px;
  }
  .card {
    width: 360px;
    height: 600px;
    background: var(--card);
    border-radius: 22px;
    position: relative;
    box-shadow: 0 14px 30px rgba(0,0,0,.45);
  }
  .card-front {
    display: flex;
    flex-direction: column;
    align-items: center;
    padding-top: 150px;
  }
  .brand-name {
    font-family: "Josefin Sans", sans-serif;
    font-weight: 300;
    font-size: 50px;
    letter-spacing: 5px;
    color: var(--white);
    line-height: 1;
  }
  .tagline-row {
    display: flex;
    align-items: center;
    gap: 8px;
    width: 270px;
    margin-top: 10px;
  }
  .tagline-row .line { flex: 1; height: 1px; background: var(--white); }
  .tagline {
    font-family: "Josefin Sans", sans-serif;
    font-size: 10px;
    letter-spacing: 4px;
    color: var(--white);
  }
  .tagline-rule { width: 270px; height: 1px; background: var(--white); margin-top: 8px; }
  .person { margin-top: 110px; text-align: center; }
  .person-name {
    font-family: "Raleway", sans-serif;
    font-weight: 600;
    font-size: 20px;
    color: var(--gold);
    letter-spacing: .5px;
  }
  .person-role {
    font-family: "Arimo", sans-serif;
    font-size: 16px;
    color: var(--white);
    margin-top: 4px;
  }
  .icon-row {
    display: flex;
    align-items: center;
    gap: 6px;
    width: 190px;
    margin-top: 20px;
  }
  .icon-row .line { flex: 1; height: 1px; background: var(--rule); }
  .icon-row svg { display: block; }
  .contact {
    font-family: "Arimo", sans-serif;
    font-size: 16px;
    color: var(--white);
    text-align: center;
    line-height: 1.35;
    margin-top: 10px;
  }
  .card-back {
    display: flex;
    align-items: flex-end;
    justify-content: center;
    padding-bottom: 150px;
  }
  .back-mark {
    font-family: "Josefin Sans", sans-serif;
    font-weight: 300;
    font-size: 26px;
    letter-spacing: 4px;
    color: var(--gold);
  }
</style>
</head>
<body>
  <section class="card card-front">
    <div class="brand-name">BRISKEL</div>
    <div class="tagline-row">
      <span class="line"></span>
      <span class="tagline">LUXURY LANDSCAPES</span>
      <span class="line"></span>
    </div>
    <div class="tagline-rule"></div>

    <div class="person">
      <div class="person-name">TOBIAS FENNICK</div>
      <div class="person-role">Co-Founder / Project Manager</div>
    </div>

    <div class="icon-row">
      <span class="line"></span>
      <svg width="24" height="24" viewBox="0 0 24 24" aria-label="Office phone">
        <rect width="24" height="24" rx="4" fill="var(--gold)"/>
        <path d="M6 9c0-2 2-3 6-3s6 1 6 3v1h-3V9H9v1H6zM7 11h10v6H7z" fill="var(--card)"/>
      </svg>
      <svg width="24" height="24" viewBox="0 0 24 24" aria-label="Mobile phone">
        <rect width="24" height="24" rx="4" fill="var(--gold)"/>
        <rect x="8" y="5" width="8" height="14" rx="1.5" fill="var(--card)"/>
        <rect x="9.5" y="7" width="5" height="9" fill="var(--gold)"/>
      </svg>
      <svg width="24" height="24" viewBox="0 0 24 24" aria-label="Email">
        <rect width="24" height="24" rx="4" fill="var(--gold)"/>
        <rect x="5" y="7" width="14" height="10" fill="var(--card)"/>
        <path d="M5 7l7 6 7-6" stroke="var(--gold)" stroke-width="1.3" fill="none"/>
      </svg>
      <span class="line"></span>
    </div>

    <div class="contact">
      <div>555-318-7094</div>
      <div>555-642-1586</div>
      <div>briskel.ca Tobias@briskel-example.ca</div>
    </div>
  </section>

  <section class="card card-back">
    <div class="back-mark">BRISKEL</div>
  </section>
</body>
</html>
```